Business Card Design for my Real Estate Investing Company

This is for a Real Estate Investing Company that will be serving the Las Vegas Valley. Id like the following slogan included: "Investing in Our Community" I have attached my logo. You will see the color tones I'm interested in..in my logo. I would like the card to be double-sided with a modern, professional look.
Target Market(s)
Homeowners, banks, real estate industry
Industry/Entity Type
Real Estate
Contact Information for Business Card
name: Dale Harwick
position: Managing Member
address: 4821 Corliss Pkwy ste 207-300
N. Las Vegas, NV 89084
phone: (702) 555-0143
fax: (702) 555-0187
email: SummitRidgeEstate@hollowmail.test
web: SummitRidgeEstates.test
*At the bottom of the card I would like....
We buy houses for cash....no repairs, no commissions, no fees!
Logo Text
SUMMIT RIDGE ESTATES "Investing in Our Community"
Font styles to use
Other font styles liked:
- Lora
Requirements
Must have
- On the back of the card, i'd like to have my logo large and the following statements:
- Are you considering selling your home? Want a simple, hassle-free transaction? We can help! We buy houses for cash and can close quickly! No need to do any repairs, no realtor commissions, no closing costs.....and no headaches. Let us help you with your real estate needs...!
Nice to have
- multiple colors 2 two tone on front and back

```html
<!DOCTYPE html>
<html lang="en">
<head>
<meta charset="utf-8">
<title>Summit Ridge Estates – Business Card</title>
<link rel="stylesheet" href="https://fonts.googleapis.com/css2?family=Lora:wght@400;500&family=Montserrat:wght@400;500&family=Oswald:wght@500&display=swap">
<style>
  :root {
    --page-bg: #e9eaec;
    --card-bg: #ffffff;
    --brand-blue: #1c5fb5;
    --brand-grey: #8f8f8f;
    --ink: #1d1d1f;
    --rule: #b9b9b9;
  }
  * { box-sizing: border-box; margin: 0; padding: 0; }
  html, body { width: 1200px; height: 900px; overflow: hidden; }
  body { background: var(--page-bg); position: relative; font-family: "Montserrat", sans-serif; color: var(--ink); }

  .card {
    position: absolute;
    width: 700px; height: 400px;
    background: var(--card-bg);
    border-radius: 28px;
    overflow: hidden;
    box-shadow: 0 6px 24px rgba(0,0,0,0.18);
  }

  /* Back side: large name mark and pitch */
  .card--back { left: 120px; top: 30px; }
  .brand-mark {
    position: absolute; left: 0; right: 0; top: 62px;
    text-align: center;
  }
  .brand-mark__name {
    display: inline-flex; align-items: center; gap: 14px;
    font-family: "Lora", serif; font-weight: 500;
    font-size: 40px; letter-spacing: 1px; color: var(--brand-blue);
  }
  .brand-mark__square { width: 24px; height: 24px; background: var(--brand-blue); }
  .brand-mark__slogan {
    margin-top: 8px;
    font-family: "Lora", serif; font-size: 17px; letter-spacing: 4px; color: var(--ink);
  }
  .pitch {
    position: absolute; left: 40px; right: 40px; top: 196px;
    text-align: center; font-size: 17.5px; line-height: 1.32; color: var(--ink);
  }

  /* Front side: contact details */
  .card--front { left: 380px; top: 470px; }
  .holder {
    position: absolute; right: 40px; top: 40px; width: 270px;
    text-align: right; border-bottom: 2px solid var(--rule); padding-bottom: 4px;
  }
  .holder__name { font-family: "Lora", serif; font-size: 30px; color: var(--brand-blue); letter-spacing: 0.5px; line-height: 1.05; }
  .holder__role { font-size: 16px; color: var(--ink); }

  .front-mark {
    position: absolute; left: 44px; top: 126px;
    display: flex; align-items: center; gap: 12px;
    font-family: "Lora", serif; font-weight: 500; font-size: 26px; color: var(--brand-blue);
  }
  .front-mark__square { width: 20px; height: 20px; background: var(--brand-blue); }

  .divider { position: absolute; left: 40px; right: 0; top: 186px; height: 1.5px; background: var(--rule); }

  .contact { position: absolute; left: 44px; top: 198px; font-size: 16.5px; line-height: 1.22; }
  .contact__address { margin-bottom: 4px; }
  .contact__row { display: flex; align-items: center; gap: 10px; }
  .contact__row svg { width: 13px; height: 13px; fill: var(--brand-blue); flex: none; }

  .tagline-band { position: absolute; left: 0; bottom: 0; width: 700px; height: 70px; }
  .tagline {
    position: absolute; left: 0; right: 0; bottom: 12px;
    text-align: center; font-family: "Oswald", sans-serif; font-weight: 500;
    font-size: 19px; letter-spacing: 1px; color: #fff; text-transform: uppercase;
  }
</style>
</head>
<body>

<section class="card card--back">
  <div class="brand-mark">
    <div class="brand-mark__name"><span class="brand-mark__square"></span>SUMMIT RIDGE ESTATES</div>
    <div class="brand-mark__slogan">“Investing in Our Community”</div>
  </div>
  <p class="pitch">
    Are you considering selling your home?<br>
    Want a simple, hassle-free transaction?<br>
    We can help! We buy houses for cash and can close quickly!<br>
    No need to do any repairs, no realtor commissions, no closing costs<br>
    and no headaches. Let us help you with your real estate needs...!
  </p>
</section>

<section class="card card--front">
  <div class="holder">
    <div class="holder__name">DALE HARWICK</div>
    <div class="holder__role">Managing Member</div>
  </div>

  <div class="front-mark"><span class="front-mark__square"></span>SUMMIT RIDGE ESTATES</div>

  <div class="divider"></div>

  <div class="contact">
    <div class="contact__address">4821 Corliss Pkwy ste 207-300<br>N. Las Vegas, NV 89084</div>
    <div class="contact__row">
      <svg viewBox="0 0 16 16"><path d="M3.5 1l3 3-1.6 1.8a9 9 0 0 0 5.3 5.3L12 9.5l3 3-2 2.5C6.5 14.5 1.5 9.5 1 3z"/></svg>
      <span>(702) 555-0143</span>
    </div>
    <div class="contact__row">
      <svg viewBox="0 0 16 16"><rect x="4" y="1" width="8" height="5"/><rect x="1" y="6" width="14" height="6" rx="1"/><rect x="4" y="10" width="8" height="5"/></svg>
      <span>(702) 555-0187</span>
    </div>
    <div class="contact__row">
      <svg viewBox="0 0 16 16"><path d="M1 3h14v10H1z M2 4l6 5 6-5" fill="none" stroke="#1c5fb5" stroke-width="1.5"/></svg>
      <span>SummitRidgeEstate@hollowmail.test</span>
    </div>
    <div class="contact__row">
      <svg viewBox="0 0 16 16"><g fill="none" stroke="#1c5fb5" stroke-width="1.4"><circle cx="8" cy="8" r="6.5"/><ellipse cx="8" cy="8" rx="3" ry="6.5"/><path d="M1.5 8h13"/></g></svg>
      <span>www.SummitRidgeEstates.test</span>
    </div>
  </div>

  <svg class="tagline-band" viewBox="0 0 700 70" preserveAspectRatio="none" aria-hidden="true">
    <path d="M0 26 Q350 18 700 4" fill="none" stroke="#b9b9b9" stroke-width="1.5"/>
    <path d="M0 33 Q350 25 700 11 L700 70 L0 70 Z" fill="#1c5fb5"/>
  </svg>
  <div class="tagline">We buy houses for cash....no repairs, no commissions, no fees!</div>
</section>

</body>
</html>
```